Hip / Cool Business Card for Custom Accessory Company

I would like to get a 2 sided design for standard size business cards, glossy (2 inches x 3.5 inches). Can be landscape or portrait layout! The design should include our logo (attached). The card should be extremely clear that the company is Tidy Pebble. Should also have our URL clear. Should also use the color scheme seen on our upcoming site, tidypebble.example. The font we use is called "hurry up." Other than that, please go-to-town. We are targeting 15-45 y.o. market, with a skew on the 20-30 crowd. We do custom and stock iPhone cases as well as Cufflinks, Winestoppers; see the website for more.
Updates

Project Deadline Extended
Reason: Extending in case the US July 4th Holiday is keeping people from working!!

Industry/Entity Type

Landscape

Requirements
Must have
• Must be clear that the website is tidypebble.example. Must be clear that custom designs are an option.
Nice to have
• images of our designs. examples of our designs.
Should not have
• hard on the eyes contrasting colors such as orange on black. green on blue. Should not have any fonts that are considered "old" like Times New Roman. But decorative fonts are fine.

```html
<!DOCTYPE html>
<html lang="en">
<head>
<meta charset="utf-8">
<title>Tidy Pebble – Business Card</title>
<link href="https://fonts.googleapis.com/css2?family=Days+One&family=Cinzel:wght@400;600&display=swap" rel="stylesheet">
<style>
  :root{
    --bg:#eceae6;
    --paper:#ffffff;
    --ink:#2f2f33;
    --teal:#1f9aa3;
    --teal-light:#2fb3b8;
    --navy:#12336b;
    --deep:#0d3f73;
    --red:#a5141c;
    --contact:#4a4a4f;
  }
  *{margin:0;padding:0;box-sizing:border-box}
  html,body{width:1200px;height:726px;overflow:hidden;background:var(--bg)}
  .canvas{position:relative;width:1200px;height:726px}
  .card{position:absolute;width:525px;height:300px;overflow:hidden;box-shadow:0 6px 18px rgba(0,0,0,.18)}
  .card--front{left:60px;top:90px;background:var(--paper)}
  .card--back{left:615px;top:336px;background:radial-gradient(ellipse at 50% 50%,var(--teal) 0%,#157f94 35%,var(--deep) 100%)}
  .waves{position:absolute;left:0;bottom:0;width:525px;height:90px}
  .brand{position:absolute;left:34px;top:28px;display:flex;align-items:center;gap:16px}
  .brand__dot{width:84px;height:84px;border-radius:50%;background:var(--teal)}
  .brand__name{font-family:"Days One",sans-serif;font-size:36px;color:var(--ink);letter-spacing:2px}
  .person{position:absolute;left:40px;top:160px;font-family:"Cinzel",serif;line-height:1.05}
  .person__name{color:var(--red);font-size:16px;font-weight:600}
  .person__role{color:var(--teal);font-size:14px;padding-left:58px}
  .divider{position:absolute;left:254px;top:124px;width:1px;height:78px;background:#c9c9c9}
  .contact{position:absolute;left:266px;top:122px;list-style:none;font-family:"Cinzel",serif;font-size:11.5px;color:var(--contact)}
  .contact li{display:flex;align-items:center;gap:7px;height:20px;white-space:nowrap}
  .contact svg{width:12px;height:12px;flex:none}
  .back-mark{position:absolute;inset:0;display:flex;align-items:center;justify-content:center;gap:14px}
  .back-mark__dot{width:96px;height:96px;border-radius:50%;background:var(--teal-light)}
  .back-mark__name{font-family:"Days One",sans-serif;font-size:38px;color:#000;letter-spacing:2px}
</style>
</head>
<body>
<main class="canvas">
  <section class="card card--front" aria-label="Card front">
    <svg class="waves" viewBox="0 0 525 90" preserveAspectRatio="none" aria-hidden="true">
      <defs>
        <linearGradient id="tealBand" x1="0" y1="0" x2="1" y2="0">
          <stop offset="0" stop-color="#0e5f86"/>
          <stop offset=".4" stop-color="#26a8b0"/>
          <stop offset="1" stop-color="#1a6d95"/>
        </linearGradient>
      </defs>
      <path d="M0 45 C140 95 320 20 525 0 L525 90 L0 90Z" fill="var(--navy)"/>
      <path d="M0 52 C140 100 320 28 525 8 L525 90 L0 90Z" fill="url(#tealBand)"/>
      <path d="M0 64 C140 106 320 40 525 22 L525 90 L0 90Z" fill="var(--navy)"/>
      <path d="M0 69 C140 110 320 46 525 28 L525 90 L0 90Z" fill="#fff"/>
      <path d="M0 74 C140 114 320 51 525 33" fill="none" stroke="var(--red)" stroke-width="4"/>
      <path d="M0 82 C140 120 320 60 525 42 L525 90 L0 90Z" fill="var(--navy)"/>
    </svg>
    <div class="brand">
      <span class="brand__dot"></span>
      <span class="brand__name">TIDY PEBBLE</span>
    </div>
    <div class="person">
      <div class="person__name">Dana Ellison</div>
      <div class="person__role">Consultant</div>
    </div>
    <span class="divider"></span>
    <ul class="contact">
      <li><svg viewBox="0 0 12 12"><circle cx="6" cy="6" r="6" fill="var(--teal)"/><path d="M4 3l1.2 1.4-.6.8c.4.9 1 1.5 1.9 1.9l.8-.6L8.7 8 8 9C5.5 8.6 3.4 6.5 3 4z" fill="#fff"/></svg>07700900415</li>
      <li><svg viewBox="0 0 12 12"><circle cx="6" cy="6" r="6" fill="var(--teal)"/><rect x="4" y="2.6" width="4" height="6.8" rx=".8" fill="#fff"/></svg>0117 496 0089</li>
      <li><svg viewBox="0 0 12 12"><circle cx="6" cy="6" r="6" fill="var(--teal)"/><rect x="3" y="4" width="6" height="4" fill="#fff"/><path d="M3 4l3 2.2L9 4" stroke="var(--teal)" stroke-width=".7" fill="none"/></svg>hello@tidypebble.example</li>
      <li><svg viewBox="0 0 12 12"><circle cx="6" cy="6" r="6" fill="var(--teal)"/><circle cx="6" cy="6" r="3" fill="none" stroke="#fff" stroke-width=".9"/><path d="M3 6h6M6 3v6" stroke="#fff" stroke-width=".7"/></svg>www.tidypebble.example</li>
    </ul>
  </section>

  <section class="card card--back" aria-label="Card back">
    <div class="back-mark">
      <span class="back-mark__dot"></span>
      <span class="back-mark__name">TIDY PEBBLE</span>
    </div>
  </section>
</main>
</body>
</html>
```